Business card design Needed for new logo / Construction business, home extensions and new builds

We need a business card design using our new logo files which i will attach to this project :)

We are a small construction business specialising in home extensions, new builds and property development. We are very ambitious and would appreciate professional and elegant designs for our new business card.

Very serious about using the services on MakerQuarry and recently acquired our new logo from here :)

Please get involved, i will feedback when i can as i am very busy but can respond daily, thanks

Target Market(s)

People that want to build onto their houses, new building developments or adding too their existing property

Industry/Entity Type

Construction

Contact Information for Business Card

Renwick Tolliver Construction, Lionel Ashby (Managing Director), Tel 07822254961, email - info@renwick-tolliver, www.renwick-tolliver.co.uk

Colors

Designer to choose colors to be used in the design.

Requirements
Must have
• I like a deep grey on the back please. A lot of you have provided black from and back, try mixing things up a little. The black looks cool 😎 Thanks

```html
<!DOCTYPE html>
<html lang="en">
<head>
<meta charset="utf-8">
<title>Renwick Tolliver Construction – Business Card</title>
<link href="https://fonts.googleapis.com/css2?family=Cinzel:wght@500&family=Poppins:wght@300;400&display=swap" rel="stylesheet">
<style>
  :root {
    --backdrop: #3a3a3a;
    --card-black: #121212;
    --pattern-dark: #1c1c1c;
    --pattern-mid: #262626;
    --silver: #d9d9d9;
    --gold: #d8a531;
    --text-light: #e6e6e6;
  }
  * { margin: 0; padding: 0; box-sizing: border-box; }
  html, body { width: 1200px; height: 959px; overflow: hidden; }
  body {
    background: var(--backdrop);
    position: relative;
    font-family: "Poppins", sans-serif;
  }
  .card {
    position: absolute;
    left: 280px;
    width: 640px;
    height: 366px;
    background: var(--card-black);
    box-shadow: 0 14px 30px rgba(0,0,0,0.45);
    overflow: hidden;
  }
  .card--back { top: 84px; }
  .card--front { top: 510px; }

  .back-pattern {
    position: absolute;
    inset: 0;
    background: linear-gradient(135deg, var(--pattern-mid) 0%, var(--pattern-dark) 55%, #0d0d0d 100%);
  }
  .back-brand {
    position: absolute;
    left: 420px;
    top: 130px;
    font-family: "Cinzel", serif;
    font-weight: 500;
    font-size: 15px;
    letter-spacing: 1px;
    color: var(--gold);
  }

  .brand-block {
    position: absolute;
    left: 40px;
    top: 140px;
    width: 270px;
    text-align: center;
    font-family: "Cinzel", serif;
    font-weight: 500;
    color: var(--silver);
    line-height: 1.25;
  }
  .brand-block .brand-mark {
    display: inline-block;
    width: 14px; height: 14px;
    border: 0;
    background: var(--gold);
    margin-bottom: 12px;
  }
  .brand-block .brand-name { font-size: 24px; letter-spacing: 1px; }
  .brand-block .brand-sub { font-size: 24px; letter-spacing: 1px; }

  .divider {
    position: absolute;
    left: 338px;
    top: 90px;
    width: 1px;
    height: 190px;
    background: var(--gold);
  }

  .contact-block {
    position: absolute;
    left: 368px;
    top: 96px;
  }
  .person-name {
    font-family: "Cinzel", serif;
    font-weight: 500;
    font-size: 20px;
    letter-spacing: 1px;
    color: var(--silver);
  }
  .person-role {
    font-size: 13px;
    color: var(--gold);
    margin-top: 2px;
  }
  .contact-list { list-style: none; margin-top: 34px; }
  .contact-list li {
    display: flex;
    align-items: center;
    gap: 8px;
    font-size: 13px;
    font-weight: 300;
    color: var(--text-light);
    margin-bottom: 8px;
  }
  .contact-list svg { width: 12px; height: 12px; flex: none; }
</style>
</head>
<body>

  <section class="card card--back" aria-label="Card back">
    <div class="back-pattern" role="img" aria-label="Tonal repeating brand pattern in dark spot gloss"></div>
    <div class="back-brand">Renwick Tolliver</div>
  </section>

  <section class="card card--front" aria-label="Card front">
    <div class="brand-block">
      <span class="brand-mark"></span>
      <div class="brand-name">Renwick Tolliver</div>
      <div class="brand-sub">Construction</div>
    </div>

    <div class="divider"></div>

    <div class="contact-block">
      <div class="person-name">Lionel Ashby</div>
      <div class="person-role">Managing Director</div>
      <ul class="contact-list">
        <li>
          <svg viewBox="0 0 24 24" aria-hidden="true"><path fill="#d8a531" d="M6.6 10.8a15.1 15.1 0 0 0 6.6 6.6l2.2-2.2c.3-.3.7-.4 1-.2 1.1.4 2.3.6 3.6.6.6 0 1 .4 1 1V20c0 .6-.4 1-1 1A17 17 0 0 1 3 4c0-.6.4-1 1-1h3.5c.6 0 1 .4 1 1 0 1.3.2 2.5.6 3.6.1.3 0 .7-.2 1z"/></svg>
          07822254961
        </li>
        <li>
          <svg viewBox="0 0 24 24" aria-hidden="true"><rect x="2" y="5" width="20" height="14" fill="#d8a531"/><path d="M2 5l10 8 10-8" fill="none" stroke="#121212" stroke-width="2"/></svg>
          info@renwick-tolliver
        </li>
        <li>
          <svg viewBox="0 0 24 24" aria-hidden="true"><g fill="none" stroke="#d8a531" stroke-width="2"><circle cx="12" cy="12" r="9"/><ellipse cx="12" cy="12" rx="4" ry="9"/><path d="M3 12h18"/></g></svg>
          www.renwick-tolliver.co.uk
        </li>
      </ul>
    </div>
  </section>

</body>
</html>
```